Professional & attention grabbing.

A business card design, front and back. I already have a logo I will attach, but I am open to something new as well.
Things to include:
Name:
Title:
Phone:
Email:
Wanting something that is professional but attention grabbing.
Also we do a lot of work using drones on natural gas pipelines (leading the future)if you want to include any of that. I'm open to ideas.
Target Market(s)
Natural gas transmission industry / greenhouse gas mitigation industry
Industry/Entity Type
Business
Colors
Designer to choose colors to be used in the design.
Look and feel
Each slider illustrates characteristics of the customer's brand and the style your logo design should communicate.

```html
<!DOCTYPE html>
<html lang="en">
<head>
<meta charset="utf-8">
<title>KV Field Inspections – Business Card</title>
<link rel="stylesheet" href="https://fonts.googleapis.com/css2?family=Montserrat:wght@800&family=Roboto:wght@400;700&display=swap">
<style>
  :root {
    --backdrop: #d8cec3;
    --card: #f0eeeb;
    --ink: #2f3032;
    --ink-soft: #444548;
    --red: #c3202a;
    --red-deep: #8a2a2e;
    --contact: #d9d4cc;
  }
  * { margin: 0; padding: 0; box-sizing: border-box; }
  html, body {
    width: 1200px; height: 1010px; overflow: hidden;
    background: var(--backdrop);
  }
  .card {
    position: absolute; left: 150px; top: 245px;
    width: 900px; height: 520px;
    background: var(--card);
    border: 1px solid #e6e3df;
    box-shadow: 0 10px 30px rgba(60, 45, 30, 0.18);
    overflow: hidden;
    font-family: "Roboto", Arial, sans-serif;
  }
  .footer-band {
    position: absolute; left: 0; right: 0; bottom: 0; height: 150px;
    background: linear-gradient(90deg,
      var(--red) 0%, var(--red-deep) 30%, var(--ink) 55%, var(--ink) 100%);
  }
  .brand {
    position: absolute; left: 59px; top: 108px;
    display: flex; align-items: center; gap: 18px;
  }
  .brand-mark { width: 54px; height: 54px; background: var(--red); }
  .brand-name {
    font-weight: 700; font-size: 40px; letter-spacing: 0.5px;
    color: var(--ink); line-height: 1;
  }
  .holder { position: absolute; left: 59px; top: 272px; }
  .holder-name {
    font-family: "Montserrat", Arial, sans-serif; font-weight: 800;
    font-size: 29px; letter-spacing: 1.5px; color: var(--red);
  }
  .holder-title { margin-top: 6px; font-size: 18px; color: var(--ink-soft); }
  .contacts {
    position: absolute; right: 40px; top: 391px;
    list-style: none; text-align: right;
  }
  .contact {
    display: flex; justify-content: flex-end; align-items: center; gap: 10px;
    font-size: 19px; color: var(--contact); height: 30px;
  }
  .contact svg { width: 18px; height: 18px; fill: var(--contact); }
</style>
</head>
<body>
  <div class="card">
    <div class="footer-band" role="img" aria-label="Decorative red and charcoal wave band along the bottom of the card"></div>

    <div class="brand">
      <span class="brand-mark"></span>
      <span class="brand-name">KV Field Inspections</span>
    </div>

    <div class="holder">
      <div class="holder-name">LAURA BRENNER</div>
      <div class="holder-title">Managing Director</div>
    </div>

    <ul class="contacts">
      <li class="contact">1300 418 502
        <svg viewBox="0 0 24 24" aria-hidden="true"><path d="M3 9c0-3 4-5 9-5s9 2 9 5v2h-5V9H8v2H3z M6 12h12l2 8H4z M10 14h4v4h-4z"/></svg>
      </li>
      <li class="contact">www.kvfieldinspect.com
        <svg viewBox="0 0 24 24" aria-hidden="true"><path d="M12 2a10 10 0 1 0 0 20 10 10 0 0 0 0-20zm0 2c1.2 1.4 2 3.5 2.2 7H9.8C10 7.5 10.8 5.4 12 4zM4.1 11a8 8 0 0 1 4-6.1C7.5 6.6 7.9 8.7 7.8 11zm0 2h3.7c.1 2.3.5 4.4 1.3 6.1a8 8 0 0 1-5-6.1zm5.7 0h4.4c-.2 3.5-1 5.6-2.2 7-1.2-1.4-2-3.5-2.2-7zm6.4 0h3.7a8 8 0 0 1-5 6.1c.8-1.7 1.2-3.8 1.3-6.1zm0-2c-.1-2.3-.5-4.4-1.3-6.1a8 8 0 0 1 5 6.1z"/></svg>
      </li>
      <li class="contact">laura.brenner@kvfieldinspect.com
        <svg viewBox="0 0 24 24" aria-hidden="true"><path d="M2 5h20v14H2z M4 7v1l8 5 8-5V7l-8 5z" fill-rule="evenodd"/></svg>
      </li>
    </ul>
  </div>
</body>
</html>
```